High Tech Real Estate Startup needs a business card

We are developing an innovative real estate marketing product based around advanced search and virtual reality.

We talk to people, we need business cards.

Target Market(s)

The target market is technology professionals and realtors.

Contact Information for Business Card

The information to be included will include

Name
Title
Phone Number
E-mail Address
www.zelquin.com

It should use simple iconography for each one of those fields.

Font styles to use
Other font styles liked:
• Co, Jubilat, Avenir

Colors

Designer to choose colors to be used in the design.

Requirements
Must have
• Clean aesthetic,
• Good use of negative space.
• It should use our company logo, shown in the attached file. It is able to use the negative of that logo (coloured font and white background) and I have attached other acceptable accent colours in a swatch file.
Should not have
• Should not be too busy
• No extraneous text (slogans, tag lines etc)

```html
<!DOCTYPE html>
<html lang="en">
<head>
<meta charset="utf-8">
<title>Zelquin Business Card</title>
<link rel="stylesheet" href="https://fonts.googleapis.com/css2?family=Roboto:wght@400;500&family=Roboto+Condensed:wght@500;700&display=swap">
<style>
  :root {
    --backdrop: #262626;
    --card-teal: #00b9bd;
    --ink-white: #ffffff;
    --ink-soft: #dff6f6;
  }
  * { box-sizing: border-box; margin: 0; padding: 0; }
  html, body {
    width: 1200px;
    height: 960px;
    overflow: hidden;
    background: var(--backdrop);
  }
  .canvas {
    position: relative;
    width: 1200px;
    height: 960px;
    background: var(--backdrop);
  }
  .card {
    position: absolute;
    left: 320px;
    width: 600px;
    background: var(--card-teal);
    color: var(--ink-white);
  }
  .card--front { top: 108px; height: 342px; }
  .card--back  { top: 493px; height: 342px; }
  .wordmark {
    position: absolute;
    left: 0;
    right: 0;
    text-align: center;
    font-family: "Roboto", sans-serif;
    font-weight: 500;
    font-size: 78px;
    letter-spacing: 3px;
    line-height: 1;
  }
  .card--front .wordmark { top: 132px; }
  .card--back .wordmark  { top: 101px; }
  .contact {
    position: absolute;
    left: 0;
    right: 0;
    top: 270px;
    text-align: center;
  }
  .contact__name {
    font-family: "Roboto Condensed", sans-serif;
    font-weight: 700;
    font-size: 20px;
    letter-spacing: 0.2px;
  }
  .contact__title {
    font-family: "Roboto Condensed", sans-serif;
    font-weight: 500;
    font-size: 15px;
  }
  .contact__details {
    margin-top: 6px;
    font-family: "Roboto", sans-serif;
    font-weight: 400;
    font-size: 14px;
    color: var(--ink-soft);
  }
</style>
</head>
<body>
  <main class="canvas">
    <section class="card card--front" aria-label="Card front">
      <div class="wordmark">ZELQUIN</div>
    </section>

    <section class="card card--back" aria-label="Card back">
      <div class="wordmark">ZELQUIN</div>
      <div class="contact">
        <p><span class="contact__name">DARA HOLM -</span> <span class="contact__title">CEO/FOUNDER</span></p>
        <p class="contact__details">555 014 2290 | dara@zelquin.com | www.zelquin.com</p>
      </div>
    </section>
  </main>
</body>
</html>
```